Velmarotix - world unique technology for better life - please let them know who am i at first sight

We need a new business card for company which is a provider of unique crystal based technology suitable for all living being. For more information and final design you can use our brochure (our colours are black and blue from brochure).
We use Verdana font

Industry/Entity Type

Business

Contact Information for Business Card

regular dimension

Font styles to use
Other font styles liked:
• Verdana

Requirements
Must have
• Logo
• name
• function/position
• phone
• mobile
• e-mail
• adress
Nice to have
• inovative design (technology directed)

```html
<!DOCTYPE html>
<html lang="en">
<head>
<meta charset="utf-8">
<title>Velmarotix Business Card</title>
<link rel="stylesheet" href="https://fonts.googleapis.com/css2?family=Noto+Sans:wght@400;700&display=swap">
<style>
  :root {
    --backdrop: #d8c9a2;
    --card-black: #0a0a0a;
    --brand-blue: #27a9e1;
    --silver-light: #e6e6e6;
    --silver-dark: #8d8d8d;
    --text-white: #f2f2f2;
    --divider: #6b6b6b;
  }
  * { margin: 0; padding: 0; box-sizing: border-box; }
  html, body { width: 1200px; height: 978px; overflow: hidden; }
  body {
    background: var(--backdrop);
    font-family: Verdana, "Noto Sans", sans-serif;
    position: relative;
  }
  .card {
    position: absolute;
    width: 560px;
    height: 320px;
    background: var(--card-black);
    border-radius: 26px;
    overflow: hidden;
  }
  .card-back { left: 320px; top: 120px; }
  .card-front { left: 320px; top: 520px; }

  .brand { display: flex; align-items: center; gap: 12px; color: var(--brand-blue); }
  .brand-dot { width: 46px; height: 46px; border-radius: 50%; background: var(--brand-blue); flex: none; }
  .brand-name { font-size: 38px; font-weight: 400; letter-spacing: 1px; line-height: 1; }

  .card-back .brand { position: absolute; left: 0; right: 0; top: 110px; justify-content: center; }
  .card-back .web {
    position: absolute; left: 0; right: 0; top: 196px;
    text-align: center; color: var(--text-white);
    font-size: 17px; font-weight: 700; letter-spacing: 1.5px;
  }

  .swoosh { position: absolute; left: 0; top: 0; width: 560px; height: 320px; }

  .card-front .brand { position: absolute; left: 196px; top: 30px; }
  .card-front .brand-dot { width: 40px; height: 40px; }
  .card-front .brand-name { font-size: 34px; }

  .person { position: absolute; left: 96px; top: 118px; color: var(--text-white); text-align: right; width: 190px; }
  .person-name { color: var(--brand-blue); font-size: 18px; font-weight: 700; margin-bottom: 4px; }
  .person-role { font-size: 13px; margin-bottom: 6px; }
  .person-address { font-size: 11.5px; line-height: 1.45; font-style: normal; }

  .divider { position: absolute; left: 300px; top: 122px; width: 1px; height: 104px; background: var(--divider); }

  .contacts { position: absolute; left: 314px; top: 120px; list-style: none; color: var(--text-white); font-size: 12px; }
  .contacts li { display: flex; align-items: center; gap: 8px; height: 21px; }
  .contact-icon { width: 15px; height: 15px; flex: none; }
</style>
</head>
<body>

<section class="card card-back" aria-label="Business card back">
  <div class="brand">
    <span class="brand-dot"></span>
    <span class="brand-name">VELMAROTIX</span>
  </div>
  <p class="web">www.velmarotix.cu</p>
</section>

<section class="card card-front" aria-label="Business card front">
  <svg class="swoosh" viewBox="0 0 560 320" aria-hidden="true">
    <defs>
      <linearGradient id="silverBand" x1="0" y1="0" x2="1" y2="1">
        <stop offset="0" stop-color="var(--silver-dark)"/>
        <stop offset="0.5" stop-color="var(--silver-light)"/>
        <stop offset="1" stop-color="var(--silver-dark)"/>
      </linearGradient>
    </defs>
    <path d="M0 112 C90 170 200 250 330 320 L0 320 Z" fill="url(#silverBand)"/>
    <path d="M0 126 C85 182 185 258 300 320 L0 320 Z" fill="var(--card-black)"/>
    <path d="M0 140 C80 196 170 262 280 320 L0 320 Z" fill="var(--brand-blue)"/>
    <path d="M0 190 C60 238 120 284 190 320 L0 320 Z" fill="url(#silverBand)"/>
    <path d="M0 204 C55 250 110 290 165 320 L0 320 Z" fill="var(--brand-blue)"/>
  </svg>

  <div class="brand">
    <span class="brand-dot"></span>
    <span class="brand-name">VELMAROTIX</span>
  </div>

  <div class="person">
    <p class="person-name">Mirela Dunavic</p>
    <p class="person-role">Founder and CEO</p>
    <address class="person-address">Street Name, City Name<br>Zipcode-01234</address>
  </div>

  <span class="divider"></span>

  <ul class="contacts">
    <li>
      <svg class="contact-icon" viewBox="0 0 16 16" aria-hidden="true"><circle cx="8" cy="8" r="8" fill="var(--text-white)"/><path d="M5 4h2l1 2.5-1.2 1a5 5 0 0 0 2.7 2.7l1-1.2L13 10v2a1 1 0 0 1-1 1A8 8 0 0 1 4 5a1 1 0 0 1 1-1z" fill="var(--card-black)"/></svg>
      012-555-0147
    </li>
    <li>
      <svg class="contact-icon" viewBox="0 0 16 16" aria-hidden="true"><circle cx="8" cy="8" r="8" fill="var(--text-white)"/><rect x="5.5" y="3" width="5" height="10" rx="1" fill="var(--card-black)"/><rect x="6.5" y="4.2" width="3" height="6" fill="var(--text-white)"/></svg>
      012-555-0148
    </li>
    <li>
      <svg class="contact-icon" viewBox="0 0 16 16" aria-hidden="true"><circle cx="8" cy="8" r="8" fill="var(--text-white)"/><rect x="3.5" y="5" width="9" height="6" fill="var(--card-black)"/><path d="M3.8 5.3 8 8.5l4.2-3.2" stroke="var(--text-white)" stroke-width="0.9" fill="none"/></svg>
      info@velmarotix.com
    </li>
    <li>
      <svg class="contact-icon" viewBox="0 0 16 16" aria-hidden="true"><circle cx="8" cy="8" r="8" fill="var(--text-white)"/><circle cx="8" cy="8" r="4.5" fill="none" stroke="var(--card-black)" stroke-width="1"/><path d="M3.5 8h9M8 3.5c-2 2.5-2 6.5 0 9M8 3.5c2 2.5 2 6.5 0 9" stroke="var(--card-black)" stroke-width="0.9" fill="none"/></svg>
      www.velmarotix.cu
    </li>
  </ul>
</section>

</body>
</html>
```